Lumra Learning Web Design Project

Who We are:
Lumra Learning is education information portal/ magazine, providing information about the Chinese and International education markets. Our aim is to help school principals improve there curriculum, and parents in understanding this curriculum.

Project Brief:
The site will include education news updates, educational services, curriculum developments and overseas study. We hope the site represents the cross cultural bridge between the west and east. The site will cover both the Sciences and Arts.

Note:
The logo design competition is also underway so we only need the website design

What We want:
This competition is for Design only no coding!
Design a home page based on Template 1,2 or 3. I only need to select one.
The design of an article page.

Optional
Design a Parvex Shutters metro style splash page.

Sites We like:
http://www.qv.com.cn/tonguebridge/default.aspx
http://www.dailyuniversitybulletin.co.uk/
http://kptz.sinocraftlearn.net/

Template Explanations:
Template 1-
The main information has a dynamic sliding category view that when clicked displays the relevant info.
In addition to the main upper menu it also has a left hand sliding menu that pops out on click or gesture

Template 2-
Has limited number of Articles most of the menus are drop downs from the top menu

Template 3-
No Top menu

Target Market(s)

Teachers, principals and parents

Industry/Entity Type

Education

Requirements
Should not have
• kindergarten preschool feel

```html
<!DOCTYPE html>
<html lang="fr">
<head>
<meta charset="utf-8">
<title>Lumra Learning</title>
<link rel="stylesheet" href="https://fonts.googleapis.com/css2?family=Ubuntu:wght@400;500;700&family=Open+Sans:wght@400;600&display=swap">
<style>
:root{
  --page:#2a2a2a;
  --white:#ffffff;
  --red:#d9342b;
  --red-dark:#b8231c;
  --red-text:#d02a22;
  --blue:#1d5b8f;
  --blue-dark:#164a76;
  --ink:#555555;
  --rule:#e2e2e2;
  --footer:#333333;
  --footer-text:#d8d8d8;
  --footer-link:#a9a9a9;
}
*{box-sizing:border-box;margin:0;padding:0}
html,body{width:930px;height:1200px;overflow:hidden}
body{background:var(--page) repeating-linear-gradient(45deg,#2d2d2d 0 2px,#272727 2px 4px);font-family:"Open Sans",sans-serif;color:var(--ink);position:relative}
.abs{position:absolute}

.site-header{left:78px;top:23px;width:774px;height:114px;background:var(--white)}
.brand{left:15px;top:60px;display:flex;align-items:center;gap:6px;font-family:"Ubuntu",sans-serif;font-weight:500;font-size:15px;color:var(--red-text);letter-spacing:.3px}
.brand-dot{width:40px;height:40px;border-radius:50%;background:var(--blue);position:absolute;left:47px;top:-44px}
.search{left:477px;top:42px;width:245px;height:27px;border:1px solid #d6d6d6;border-radius:2px;font-size:9px;font-style:italic;color:#9a9a9a;padding:8px 9px}
.search-btn{left:728px;top:42px;width:30px;height:27px;background:var(--red-dark);border-radius:2px}

.side-nav{left:78px;top:146px;width:178px;height:386px;background:var(--red)}
.nav-item{height:55.1px;display:flex;align-items:center;border-bottom:1px solid #c42c24;font-family:"Ubuntu",sans-serif;font-weight:500;font-size:13.5px;color:#fff}
.nav-icon{width:47px;height:100%;background:var(--red-dark);display:flex;align-items:center;justify-content:center;margin-right:12px}
.social-row{left:78px;top:548px;display:flex;gap:20px}
.social-row span{width:20px;height:20px;border-radius:50%;background:#f2f2f2}

.main{left:263px;top:146px;width:589px;height:793px;background:var(--white)}
.slider{left:9px;top:8px;width:440px;height:232px;background:linear-gradient(110deg,#c7d9e8 0%,#e7eef4 35%,#8fb0c9 70%,#dfe7ee 100%)}
.slider h1{position:absolute;left:201px;top:32px;font-family:"Ubuntu",sans-serif;font-weight:700;font-size:21px;line-height:26px;color:var(--blue)}
.btn-read{position:absolute;left:202px;top:84px;background:var(--blue);color:#fff;font-family:"Ubuntu",sans-serif;font-weight:500;font-size:11px;padding:5px 7px;border-radius:2px}

.section-bar{left:9px;width:441px;height:32px;display:flex;align-items:center;justify-content:space-between;padding:0 10px;font-family:"Ubuntu",sans-serif;font-weight:700;font-size:18px;color:#fff}
.section-bar.blue{background:linear-gradient(#2a6ea8,var(--blue-dark))}
.section-bar.red{background:linear-gradient(#d8322a,var(--red-dark))}
.view-all{background:#fff;color:#222;font-size:9px;font-weight:700;padding:3px 5px;border-radius:2px}
.section-bar::after{content:"";position:absolute;left:0;bottom:-7px;border-top:7px solid inherit;border-right:7px solid transparent}
.section-bar.blue::after{border-top-color:var(--blue-dark)}
.section-bar.red::after{border-top-color:var(--red-dark)}

.card{width:216px;border:1px solid var(--rule);border-bottom-width:2px;background:#fff;padding:8px}
.card .photo{height:98px;margin-bottom:10px}
.card.news .photo{height:74px}
.card h3{font-family:"Ubuntu",sans-serif;font-weight:500;font-size:10.4px;line-height:14px;color:var(--red-text);text-transform:uppercase;padding:0 2px}
.card.news h3{color:var(--blue)}
.card p{font-size:9px;line-height:15.5px;color:#666;padding:4px 2px 0}
.meta{display:flex;gap:12px;font-family:"Ubuntu",sans-serif;font-size:10px;color:var(--blue);padding:6px 2px 0}
.date-red{font-family:"Open Sans",sans-serif;font-size:8.5px;color:var(--red-text);padding:2px 2px 0}

.ad{left:721px;width:124px;color:#fff;font-family:"Ubuntu",sans-serif;text-align:center}
.ad-red{top:154px;height:464px;background:var(--red)}
.ad-blue{top:626px;height:304px;background:#0f4c8a}
.ad-label{background:#fff;color:var(--blue);font-weight:700;font-size:14px;padding:10px 4px;margin:12px 6px 0}

.site-footer{left:78px;top:948px;width:774px;height:234px;background:var(--footer)}
.col{top:26px;font-family:"Ubuntu",sans-serif;color:var(--footer-text);font-size:12px}
.col ul{list-style:none;margin-top:16px}
.col li{font-family:"Open Sans",sans-serif;font-size:8.5px;line-height:16.3px;color:var(--footer-link);text-decoration:underline}
.net{display:flex;gap:10px;margin-top:17px}
.net span{width:25px;height:25px;background:#4a8fc4;border-radius:2px}
.newsletter{display:flex;margin-top:10px;width:205px;height:25px;background:#2a2a2a;border:1px solid #3e3e3e}
.newsletter span{flex:1;font-family:"Open Sans",sans-serif;font-size:8px;font-style:italic;color:#777;padding:7px 9px}
.newsletter b{background:var(--red-dark);color:#fff;font-weight:400;font-size:10px;padding:5px 10px}
.footer-rule{left:15px;top:189px;width:744px;height:1px;background:#4a4a4a}
.copy{left:15px;top:209px;font-size:9px;color:#aaa}
</style>
</head>
<body>

<header class="site-header abs">
  <div class="brand abs"><span class="brand-dot"></span>LUMRA LEARNING</div>
  <div class="search abs">Please enter your search</div>
  <div class="search-btn abs">
    <svg width="30" height="27" viewBox="0 0 30 27"><circle cx="14" cy="12" r="5" fill="none" stroke="#fff" stroke-width="2"/><line x1="17.5" y1="15.5" x2="20" y2="18" stroke="#fff" stroke-width="2.5"/></svg>
  </div>
</header>

<nav class="side-nav abs">
  <div class="nav-item"><span class="nav-icon"><svg width="28" height="26" viewBox="0 0 28 26" fill="none" stroke="#fff" stroke-width="2"><path d="M3 13 14 3l11 10M6 11v12h16V11"/></svg></span>Home</div>
  <div class="nav-item"><span class="nav-icon"><svg width="28" height="26" viewBox="0 0 28 26" fill="#fff"><ellipse cx="15" cy="11" rx="11" ry="8"/><path d="M6 16 4 24l8-5z"/></svg></span>About Us</div>
  <div class="nav-item"><span class="nav-icon"><svg width="28" height="26" viewBox="0 0 28 26" stroke="#fff" stroke-width="3"><line x1="4" y1="4" x2="24" y2="22"/><line x1="24" y1="4" x2="4" y2="22"/></svg></span>Service</div>
  <div class="nav-item"><span class="nav-icon"><svg width="28" height="26" viewBox="0 0 28 26" fill="none" stroke="#fff" stroke-width="2"><rect x="7" y="2" width="14" height="22"/><path d="M10 10h8M10 14h8M10 18h8"/></svg></span>New &amp; Event</div>
  <div class="nav-item"><span class="nav-icon"><svg width="28" height="26" viewBox="0 0 28 26" fill="none" stroke="#fff" stroke-width="2"><rect x="3" y="4" width="22" height="18"/><path d="M3 9h22M7 13h14M7 17h6"/></svg></span>Blog</div>
  <div class="nav-item"><span class="nav-icon"><svg width="28" height="26" viewBox="0 0 28 26" fill="none" stroke="#fff" stroke-width="2"><rect x="4" y="3" width="20" height="13"/><path d="M14 16v8M9 24l5-8 5 8M8 8h7M8 11h11"/></svg></span>Lumra Learning</div>
  <div class="nav-item"><span class="nav-icon"><svg width="28" height="26" viewBox="0 0 28 26" fill="#fff"><path d="M20 3l4 4-5 5-3-2-6 6 2 3-5 5-4-4C4 14 12 6 20 3z"/></svg></span>Contact Us</div>
</nav>
<div class="social-row abs" aria-label="Social links"><span></span><span></span><span></span><span></span><span></span></div>

<main class="main abs">
  <div class="slider abs" role="img" aria-label="Smiling student resting her chin on a stack of books">
    <h1>Contrairement à unei<br>nion répandue</h1>
    <span class="btn-read">Read More</span>
  </div>

  <div class="section-bar blue abs" style="top:248px">Latest Articles<span class="view-all">View All</span></div>
  <article class="card abs" style="left:9px;top:296px;height:254px">
    <div class="photo" role="img" aria-label="Student with glasses smiling outdoors" style="background:linear-gradient(90deg,#b0544a,#8f6a58 50%,#c57b63)"></div>
    <h3>Plusieurs variations de Lorem Ipsum peuvent être trouvées ici ou.</h3>
    <p>Le Lorem Ipsum est simplement du faux texte employé dans la composition et la mise en page avant impressionLe Lorem Ipsum est le faux texte standard.</p>
    <div class="meta"><span>&#9679; By Admin</span><span>&#9719; June 24, 2013</span></div>
  </article>
  <article class="card abs" style="left:234px;top:296px;height:254px">
    <div class="photo" role="img" aria-label="Two students reading together in a classroom" style="background:linear-gradient(90deg,#6a4a3a,#b58a6c 50%,#7d6a86)"></div>
    <h3>Ensemble des morceaux de texte pour réaliser un livre spécimen de.</h3>
    <p>Contrairement à une opinion répandue, le Lorem Ipsum n'est pas simplement du texte aléatoire. Il trouve ses racines dans une oeuvre de la.</p>
    <div class="meta"><span>&#9679; By Admin</span><span>&#9719; June 24, 2013</span></div>
  </article>

  <div class="section-bar red abs" style="top:560px">Latest News<span class="view-all">View All</span></div>
  <article class="card news abs" style="left:9px;top:608px;height:176px">
    <div class="photo" role="img" aria-label="Student writing an exam at a desk" style="background:linear-gradient(90deg,#5a4b45,#9a8f88 50%,#c9b08a)"></div>
    <h3>Plusieurs variations de Lorem Ipsum peuvent</h3>
    <div class="date-red">&#9719; June 24, 2013</div>
    <p style="padding-top:2px">Le Lorem Ipsum est simplement du faux texte employé dans.</p>
  </article>
  <article class="card news abs" style="left:234px;top:608px;height:176px">
    <div class="photo" role="img" aria-label="Students working in a library" style="background:linear-gradient(90deg,#b68a5e,#6b5a4f 50%,#2f2f33)"></div>
    <h3>De nombreuses suites logicielles de mise en page</h3>
    <div class="date-red">&#9719; June 24, 2013</div>
    <p style="padding-top:2px">Le Lorem Ipsum est simplement du faux texte employé dans la composition et.</p>
  </article>
</main>

<aside class="ad ad-red abs">
  <div class="ad-label" style="color:#1d6fb0">Tovi Tees</div>
  <div role="img" aria-label="Illustration of a shouting supporter" style="height:230px;margin:12px 0 0;background:linear-gradient(#c92d24,#f1e4dc 55%,#c92d24)"></div>
  <div style="font-weight:700;font-size:32px;line-height:34px;margin-top:10px">PRIDE</div>
  <div style="font-weight:700;font-size:9px">NORTHFIELD IS RED</div>
  <div style="font-size:21px;line-height:26px;margin-top:24px">Get the<br>shirt now!</div>
</aside>
<aside class="ad ad-blue abs">
  <div role="img" aria-label="Off-road truck and quad bike silhouettes" style="height:190px;margin:20px 20px 0;background:linear-gradient(#0f4c8a,#6e95bd 50%,#0f4c8a)"></div>
  <div class="ad-label" style="color:#a0331e;margin-top:14px">Mudvale</div>
  <div style="font-weight:500;font-size:13px;line-height:15px;margin-top:10px">The Off-Road<br>Encyclopedia</div>
</aside>

<footer class="site-footer abs">
  <div class="col abs" style="left:15px">Company<ul><li>Contrairement</li><li>Opinion répandue</li><li>Pas simplement du</li><li>Texte aléatoire</li></ul></div>
  <div class="col abs" style="left:149px">Dictionnaire de<ul><li>Plusieurs variations</li><li>De Lorem Ipsum</li><li>Vent être</li></ul></div>
  <div class="col abs" style="left:291px">Trouvées ici ou<ul><li>Siècle est reproduit</li><li>Dessous pour les</li><li>CurieuxPlusieurs varia-</li><li>tions</li><li>De Lorem Ipsum</li></ul></div>
  <div class="col abs" style="left:428px">Embarassantes<ul><li>L'extrait standard</li><li>Utilisé depuis</li><li>Siècle est reproduit</li><li>Dessous pour les</li><li>Curieux</li><li>Vous voulez utiliser</li><li>Passage du Lorem</li></ul></div>
  <div class="col abs" style="left:556px">Stay updates on our Socail Network
    <div class="net" aria-label="Social networks"><span></span><span></span><span></span></div>
    <div style="margin-top:14px">Join Our Newsletter</div>
    <div class="newsletter"><span>Enter your email address</span><b>Subscribe</b></div>
  </div>
  <div class="footer-rule abs"></div>
  <div class="copy abs">© Copyrights 2013 All rights Reserved</div>
</footer>

</body>
</html>
```